KLR Buildworks - Civil Construction Construction Company (Telecommunications)

Need a basic website to refine our branding to a current reflection of our service offerings. KLR Buildworks provides civil construction services specializing in telecommunication sector.
I have started to create a website using word press. I would like to have someone refine the design and polish the overall look and functionality of the site. I would like to website to function in the wordpress format to allow for future edits and control of site.
Included site preview:
https://pvhosts-ua.pagemakerbench.example/7e2d94fa.com/Admin/index.html/qm_draft_view

```html
<!DOCTYPE html>
<html lang="en">
<head>
<meta charset="utf-8">
<title>KLR Buildworks – Civil Construction</title>
<link href="https://fonts.googleapis.com/css2?family=Montserrat:wght@400;500;600;700;800&family=Lato:wght@400;700&display=swap" rel="stylesheet">
<style>
:root{
  --red:#ec1c24;
  --dark:#111214;
  --ink:#222;
  --grey:#555;
  --panel:#f2f2f2;
  --white:#fff;
}
*{box-sizing:border-box;margin:0;padding:0}
html,body{width:1200px;height:3624px;overflow:hidden}
body{position:relative;background:var(--white);font-family:'Montserrat',sans-serif;color:var(--ink)}
.abs{position:absolute}

/* header */
.top-line{left:0;top:0;width:1200px;height:5px;background:var(--red)}
.brand{left:111px;top:28px;display:flex;align-items:center;gap:10px;font-family:'Montserrat',sans-serif;font-weight:600;font-size:28px;color:var(--dark);letter-spacing:.5px}
.brand-mark{width:22px;height:22px;background:var(--red)}
.nav{left:514px;top:36px;display:flex;gap:28px;font-size:14px;font-weight:600;color:var(--dark)}
.nav a{color:inherit;text-decoration:none;position:relative}
.nav a.active::after{content:"";position:absolute;left:-6px;right:-6px;bottom:-9px;height:4px;background:var(--red);transform:skewX(-30deg)}

/* hero */
.hero{left:0;top:87px;width:1200px;height:557px;background:linear-gradient(180deg,#4f79c4 0%,#8eaad4 22%,#c59a3a 40%,#6f7a34 62%,#4a5a25 100%)}
.hero-plate{left:320px;top:287px;width:560px;height:130px;background:rgba(20,20,20,.55);clip-path:polygon(6% 0,94% 0,88% 100%,12% 100%)}
.hero-title{left:0;top:300px;width:1200px;text-align:center;font-size:54px;font-weight:700;color:var(--white);letter-spacing:1px}
.hero-phone{left:508px;top:375px;width:184px;height:43px;background:var(--white);display:flex;align-items:center;font-size:14px;font-weight:600}
.hero-phone .ico{width:40px;height:43px;background:var(--red);display:flex;align-items:center;justify-content:center;margin-right:12px}
.slide-arrow{width:44px;height:44px;border-radius:50%;background:rgba(255,255,255,.35);display:flex;align-items:center;justify-content:center}
.hero-band{left:0;top:640px;width:1200px;height:72px}

/* company profile */
.profile-bg{left:560px;top:712px;width:640px;height:616px;background:linear-gradient(90deg,#fff 0%,#f6f2f2 100%)}
.profile-frame{left:136px;top:848px;width:372px;height:393px;background:var(--red)}
.profile-photo{left:180px;top:713px;width:371px;height:486px;background:linear-gradient(160deg,#6c6c6c 0%,#8a2a22 45%,#b23a2c 65%,#3b3f2e 100%)}
.h2{font-size:40px;font-weight:700;color:var(--dark);letter-spacing:.5px}
.h2-bar{height:6px;background:var(--red);clip-path:polygon(0 0,100% 0,82% 100%,8% 100%)}
.profile-title{left:600px;top:796px}
.profile-bar{left:600px;top:848px;width:114px}
.profile-text{left:598px;top:884px;width:506px;font-family:'Lato',sans-serif;font-size:13.4px;line-height:21.4px;color:var(--grey);text-align:justify}
.btn-more{left:598px;top:1199px;width:184px;height:43px;background:var(--red);color:var(--white);font-size:14px;font-weight:600;display:flex;align-items:center;padding-left:21px}
.btn-more .arr{position:absolute;right:4px;top:4px;width:38px;height:35px;background:var(--white);display:flex;align-items:center;justify-content:center}

/* why */
.why{left:0;top:1328px;width:1200px;height:664px;background:linear-gradient(180deg,#1c1f1c 0%,#2a2e29 50%,#1a1b1a 100%)}
.why-title{left:0;top:1404px;width:1200px;text-align:center;color:var(--white)}
.why-bar{left:547px;top:1454px;width:110px}
.card{top:1505px;width:308px;height:224px}
.card-photo{width:100%;height:100%}
.card-flag{position:absolute;left:0;top:0;width:146px;height:140px;background:var(--red);clip-path:polygon(0 0,100% 0,0 100%)}
.card-flag svg{position:absolute;left:20px;top:18px}
.bullets{top:1752px;list-style:none;color:var(--white);font-size:15px;line-height:20px}
.bullets li{position:relative;padding-left:25px;margin-bottom:19px}
.bullets li::before{content:"";position:absolute;left:0;top:4px;width:12px;height:12px;border-radius:50%;background:var(--red)}
.bullets li::after{content:"";position:absolute;left:3px;top:7px;width:5px;height:3px;border-left:1.6px solid #fff;border-bottom:1.6px solid #fff;transform:rotate(-45deg)}

/* work */
.work-title{left:0;top:2068px;width:1200px;text-align:center}
.work-bar{left:547px;top:2118px;width:110px}
.work-intro{left:111px;top:2168px;width:977px;height:130px;background:var(--panel);padding:28px 36px;font-size:20px;line-height:26px;color:#444}
.work-photo{left:111px;top:2298px;width:977px;height:401px;background:linear-gradient(180deg,#c6c8c6 0%,#aeb1ad 45%,#6f8c56 70%,#5d5f5c 100%)}
.work-caption{left:445px;top:2638px;width:643px;height:61px;background:var(--red);clip-path:polygon(6% 0,100% 0,100% 100%,0 100%);color:var(--white);font-size:15.5px;font-weight:600;display:flex;align-items:center;padding-left:54px}
.thumb{top:2717px;height:181px}
.thumb.active{outline:3px solid var(--red);outline-offset:0}
.work-arrow{top:2784px;background:#777}

/* contact */
.contact-band{left:0;top:2970px;width:1200px;height:80px}
.contact{left:0;top:3046px;width:1200px;height:578px;background:#000}
.contact-title{left:111px;top:3122px;color:var(--white)}
.contact-bar{left:111px;top:3172px;width:114px}
.map{left:111px;top:3215px;width:488px;height:293px;background:linear-gradient(135deg,#dfe7dc 0%,#e9ece6 50%,#cfe0c9 100%)}
.contact-note{left:627px;top:3128px;width:460px;font-size:14.5px;line-height:21px;color:var(--white)}
.field{border:2px solid var(--red);color:var(--white);font-size:15px;padding:20px 19px}
.send{left:1033px;top:3451px;width:55px;height:57px;background:var(--red);display:flex;align-items:center;justify-content:center}
.social{left:111px;top:3560px;display:flex;gap:6px}
.social span{width:29px;height:29px;border-radius:50%;background:var(--white)}
.copyright{left:700px;top:3567px;width:392px;text-align:right;color:var(--white);font-size:12.5px}
</style>
</head>
<body>

<header>
  <div class="abs top-line"></div>
  <div class="abs brand"><span class="brand-mark"></span>KLR BUILDWORKS</div>
  <nav class="abs nav">
    <a class="active" href="#">HOME</a>
    <a href="#">COMPANY PROFILE</a>
    <a href="#">WHY CHOOSE US</a>
    <a href="#">OUR WORK</a>
    <a href="#">CONTACT</a>
  </nav>
</header>

<section>
  <div class="abs hero" role="img" aria-label="Tracked cable-laying dozer with a red conduit reel on a grassy field under blue sky"></div>
  <div class="abs hero-plate"></div>
  <h1 class="abs hero-title">KLR BUILDWORKS</h1>
  <div class="abs hero-phone"><span class="ico"><svg width="14" height="14" viewBox="0 0 24 24"><path fill="#fff" d="M6.6 10.8a15 15 0 0 0 6.6 6.6l2.2-2.2a1 1 0 0 1 1-.25 11.4 11.4 0 0 0 3.6.57 1 1 0 0 1 1 1V20a1 1 0 0 1-1 1A17 17 0 0 1 3 4a1 1 0 0 1 1-1h3.5a1 1 0 0 1 1 1c0 1.25.2 2.45.57 3.57a1 1 0 0 1-.25 1z"/></svg></span>+1 555 010 2040</div>
  <div class="abs slide-arrow" style="left:112px;top:344px"><svg width="10" height="14"><path d="M7 2 2 7l5 5" stroke="#333" stroke-width="1.5" fill="none"/></svg></div>
  <div class="abs slide-arrow" style="left:1042px;top:344px"><svg width="10" height="14"><path d="M3 2l5 5-5 5" stroke="#333" stroke-width="1.5" fill="none"/></svg></div>
  <svg class="abs hero-band" viewBox="0 0 1200 72" preserveAspectRatio="none"><polygon points="0,0 1200,0 1115,70 0,30" fill="#ec1c24"/></svg>
</section>

<section>
  <div class="abs profile-bg"></div>
  <div class="abs profile-frame"></div>
  <div class="abs profile-photo" role="img" aria-label="Crew member in hi-vis gear operating a red trenching machine"></div>
  <h2 class="abs h2 profile-title">COMPANY PROFILE</h2>
  <div class="abs h2-bar profile-bar"></div>
  <p class="abs profile-text">Each of KLR's construction crews are dispatched with a full complement of late model equipment and tools required to complete civil underground construction projects in a safe and efficient manner meeting all criteria established by client, governing bodies and site environments. We constantly maintain and update our fleet to supply our clients with the most effective and modern construction solutions possible. Our dedicated maintenance team ensures we are compliant across our wide areas of operation.All this achieved without compromising safety or quality. We understand the unique challenges of deploying crews and completing civil construction projects within Western Canada's diverse geography, terrain and climate. Our experience helps us achieve success in some of the most challenging situations and conditions. Safety is a top priority, closely tied to our day- to-day operations. We believe that effective implementation of Health, Safety and Environmental plans are critical to the success of any project, no matter the size or scope.</p>
  <div class="abs btn-more">LEARN MORE<span class="arr"><svg width="14" height="12" viewBox="0 0 14 12"><path d="M1 6h10M7 2l4 4-4 4" stroke="#ec1c24" stroke-width="2" fill="none"/></svg></span></div>
</section>

<section>
  <div class="abs why" role="img" aria-label="Dark-toned backdrop of a worksite with trees"></div>
  <h2 class="abs h2 why-title">WHY CHOOSE US</h2>
  <div class="abs h2-bar why-bar"></div>

  <div class="abs card" style="left:111px">
    <div class="card-photo" role="img" aria-label="Red tracked trencher under a cloudy sky" style="background:linear-gradient(160deg,#7aa1cf 0%,#c8d3df 40%,#a3281f 70%,#3d3a32 100%)"></div>
    <div class="card-flag"><svg width="44" height="44" viewBox="0 0 24 24" fill="none" stroke="#fff" stroke-width="2"><rect x="4" y="3" width="12" height="17"/><path d="M7 8h6M7 12h4M14 16l6-8 2 2-6 8h-2z"/></svg></div>
  </div>
  <div class="abs card" style="left:446px">
    <div class="card-photo" role="img" aria-label="Operator in hi-vis vest beside drilling equipment near trees" style="background:linear-gradient(170deg,#b8cbe0 0%,#7f9a63 45%,#2a2b2a 100%)"></div>
    <div class="card-flag"><svg width="42" height="42" viewBox="0 0 24 24" fill="none" stroke="#fff" stroke-width="2"><path d="M4 20l9-9M14 4a4 4 0 0 0 6 5l-3-3zM4 4l4 4M6 2l4 4-2 2-4-4zM14 14l6 6"/></svg></div>
  </div>
  <div class="abs card" style="left:780px">
    <div class="card-photo" role="img" aria-label="White service pickup truck with utility body" style="background:linear-gradient(170deg,#c9d3dc 0%,#eef0f2 40%,#9fa39b 75%,#3d3f3a 100%)"></div>
    <div class="card-flag"><svg width="42" height="42" viewBox="0 0 24 24" fill="#fff"><path d="M12 3a8 8 0 0 0-8 8v2h16v-2a8 8 0 0 0-8-8z"/><rect x="2" y="14" width="20" height="3"/><circle cx="12" cy="11" r="2.5" fill="#ec1c24"/></svg></div>
  </div>

  <ul class="abs bullets" style="left:111px;width:210px">
    <li>Accredited health and safety program</li>
    <li>Proven track record of safety excellence</li>
    <li>Continuous training and development of employees</li>
  </ul>
  <ul class="abs bullets" style="left:446px;width:250px">
    <li>Productive and efficient crews</li>
    <li style="margin-bottom:19px">Current fleet of modern equipment</li>
    <li>Use of latest construction techniques/technologies</li>
  </ul>
  <ul class="abs bullets" style="left:780px;width:300px">
    <li>Quality and process driven</li>
    <li>Excellent customer service</li>
    <li>Privately owned and operated</li>
    <li>Dependable, Reliable and Honest</li>
  </ul>
</section>

<section>
  <h2 class="abs h2 work-title">OUR WORK</h2>
  <div class="abs h2-bar work-bar"></div>
  <p class="abs work-intro">KLR Buildworks is equipped to complete civil construction projects of all sizes and complexities. From small alterations and repairs to large scale network deployments throughout large geographical areas.</p>
  <div class="abs work-photo" role="img" aria-label="Hydrovac truck and crew working on a roadside verge in front of retail buildings"></div>
  <div class="abs work-caption">Hydrovacs Utilized to Safely Expose and Identify Buried Infrastructure</div>

  <div class="abs thumb active" style="left:110px;width:232px;background:linear-gradient(180deg,#c3c5c3 0%,#8f9b86 60%,#5e605d 100%)" role="img" aria-label="Hydrovac truck on site"></div>
  <div class="abs thumb" style="left:360px;width:230px;background:linear-gradient(180deg,#8fb0d8 0%,#b49b4a 45%,#66712f 100%)" role="img" aria-label="Tracked cable plough in a field"></div>
  <div class="abs thumb" style="left:608px;width:231px;background:linear-gradient(180deg,#6f8e4b 0%,#c7a326 55%,#3c3a2a 100%)" role="img" aria-label="Yellow drill rig with crew"></div>
  <div class="abs thumb" style="left:858px;width:230px;background:linear-gradient(135deg,#8a8d87 0%,#3f9fc4 55%,#2c5f7a 100%)" role="img" aria-label="Blue pump unit close-up"></div>
  <div class="abs slide-arrow work-arrow" style="left:33px"><svg width="10" height="14"><path d="M7 2 2 7l5 5" stroke="#fff" stroke-width="1.5" fill="none"/></svg></div>
  <div class="abs slide-arrow work-arrow" style="left:1119px"><svg width="10" height="14"><path d="M3 2l5 5-5 5" stroke="#fff" stroke-width="1.5" fill="none"/></svg></div>
</section>

<footer>
  <svg class="abs contact-band" viewBox="0 0 1200 80" preserveAspectRatio="none"><polygon points="85,8 1200,50 1200,80 0,80 0,70" fill="#ec1c24"/></svg>
  <div class="abs contact"></div>
  <h2 class="abs h2 contact-title">CONTACT US</h2>
  <div class="abs h2-bar contact-bar"></div>
  <div class="abs map" role="img" aria-label="Street map showing the office location"></div>
  <p class="abs contact-note">If you would like to know more about our services please call or provide the information below. Thank you for your interest in KLR Buildworks</p>
  <div class="abs field" style="left:629px;top:3216px;width:219px;height:57px">Name</div>
  <div class="abs field" style="left:869px;top:3216px;width:219px;height:57px">Email</div>
  <div class="abs field" style="left:629px;top:3295px;width:459px;height:56px">Address</div>
  <div class="abs field" style="left:629px;top:3372px;width:459px;height:136px">Message</div>
  <div class="abs send"><svg width="16" height="16" viewBox="0 0 24 24"><path fill="#fff" d="M22 2 2 11l7 3 2 8 3-6 6 3z"/></svg></div>
  <div class="abs social"><span></span><span></span><span></span></div>
  <p class="abs copyright">© Copyrights 2022 Company name | All Rights reserved</p>
</footer>

</body>
</html>
```